Gift Cards in the Mail Envelope

Mailing out gift cards in the envelope. Need an eye popping envelope. Please look at the enclosed images. The envelope should look like that.

Low design quality

```html
<!DOCTYPE html>
<html lang="en">
<head>
<meta charset="UTF-8">
<title>Gift Card Mailer Envelope</title>
<style>
  :root {
    --canvas-bg: #e4e4e4;
    --envelope-teal: #037a6f;
    --envelope-teal-light: #0a9486;
    --envelope-teal-deep: #025f57;
    --window-tint: #dbfcfc;
    --accent-mint: #7ff0e2;
    --envelope-white: #ffffff;
    --edge-shadow: rgba(0, 0, 0, 0.28);
  }
  html, body {
    margin: 0;
    padding: 0;
    overflow: hidden;
  }
  .canvas {
    position: relative;
    width: 1200px;
    height: 1200px;
    background: var(--canvas-bg);
    overflow: hidden;
  }
  .envelope-front {
    position: absolute;
    left: 190px;
    top: 192px;
    width: 817px;
    height: 410px;
    background: linear-gradient(135deg, var(--envelope-teal-light) 0%, var(--envelope-teal) 45%, var(--envelope-teal-deep) 100%);
    box-shadow: 0 3px 6px var(--edge-shadow);
    overflow: hidden;
  }
  .front-accent {
    position: absolute;
    inset: 0;
    width: 817px;
    height: 410px;
  }
  .front-accent .accent-band {
    fill: var(--accent-mint);
    opacity: 0.16;
  }
  .front-accent .accent-rule {
    fill: none;
    stroke: var(--accent-mint);
    stroke-width: 3;
    opacity: 0.7;
  }
  .address-window {
    position: absolute;
    left: 60px;
    top: 55px;
    width: 388px;
    height: 175px;
    background: var(--window-tint);
    box-shadow: 0 0 0 4px rgba(127, 240, 226, 0.45);
  }
  .envelope-back {
    position: absolute;
    left: 192px;
    top: 704px;
    width: 814px;
    height: 404px;
    background: var(--envelope-white);
    box-shadow: 0 3px 6px var(--edge-shadow);
  }
  .envelope-flap {
    position: absolute;
    left: 0;
    top: 0;
    width: 814px;
    height: 210px;
  }
  .envelope-flap .flap-shape {
    fill: url(#flapShade);
  }
  .envelope-flap .flap-trim {
    fill: none;
    stroke: var(--accent-mint);
    stroke-width: 3;
    opacity: 0.75;
  }
</style>
</head>
<body>
  <main class="canvas">
    <section class="envelope-front" aria-label="Envelope front">
      <svg class="front-accent" viewBox="0 0 817 410" aria-hidden="true">
        <polygon class="accent-band" points="560,410 817,150 817,230 640,410"/>
        <polygon class="accent-band" points="680,410 817,272 817,318 726,410"/>
        <path class="accent-rule" d="M60 290 H448"/>
      </svg>
      <div class="address-window"></div>
    </section>
    <section class="envelope-back" aria-label="Envelope back">
      <svg class="envelope-flap" viewBox="0 0 814 210" aria-hidden="true">
        <defs>
          <linearGradient id="flapShade" x1="0" y1="0" x2="0" y2="1">
            <stop offset="0" stop-color="#0a9486"/>
            <stop offset="1" stop-color="#037a6f"/>
          </linearGradient>
        </defs>
        <path class="flap-shape" d="M6 0 H808 V40 Q808 54 794 58 L414 206 Q408 209 400 206 L20 58 Q6 54 6 40 Z"/>
        <path class="flap-trim" d="M30 40 L407 186 L784 40"/>
      </svg>
    </section>
  </main>
</body>
</html>
```